Hello my name is Colin, I am Starting a business called Lumen Wellness and fitness and am in need of a memorable business card.
It is a personal training studio. I have added the logo that i would like to be on the left center om my business card. i would like room left up the top for a heading sentence such as. "Is your body shocking for all the wrong reasons". there must be room left on the right of the logo below the main heading for 3 sub headings.
then under those 3 headings and logo room for another larger heading eg. "give me a call and learn how to eat chocolate, drink bear and have great sex". in what room is left i would like to be used for my contact details, use I'm Colin Ferrante your fitness expert on the left then on the right Phone, Email and website space in at least 12 Point. Very specific i know :) now onto the back, for the back i would like an eye catching graphic and room for one main headline and 3 bullet points centered just write anything i will choose what to put in them when i pick a winner. Thank you very much for sticking through all of that :) i appreciate you taking the time to read it and hopefully undergo designing me a business card.
I can't wait to see the designs!

Target Market(s)

slightly more towards females although it would probably be best if it was targeted towards both sexes

Industry/Entity Type

Training

Requirements
Nice to have
• I would love to see if anyone could come up with a design that would really make my card stand out and be memorable.
Should not have
• tacky fitness photos of abs and muscles etc.

```html
<!DOCTYPE html>
<html lang="en">
<head>
<meta charset="utf-8">
<title>Lumen Wellness and Fitness – Business Card</title>
<link href="https://fonts.googleapis.com/css2?family=Questrial&family=Open+Sans:wght@400;600&display=swap" rel="stylesheet">
<style>
  :root {
    --backdrop: #d8d2cb;
    --card: #ffffff;
    --brand-blue: #1d4f86;
    --brand-blue-deep: #163f6e;
    --band-dark: #2b2b2b;
    --ink: #333333;
    --ink-soft: #555555;
    --label: #1a1a1a;
  }
  * { margin: 0; padding: 0; box-sizing: border-box; }
  html, body { width: 1200px; height: 788px; overflow: hidden; }
  body {
    background: var(--backdrop);
    font-family: "Questrial", "Century Gothic", sans-serif;
    color: var(--ink);
    position: relative;
  }
  .view-label {
    position: absolute;
    font-family: "Open Sans", Arial, sans-serif;
    font-size: 21px;
    color: var(--label);
    transform: translateX(-50%);
  }
  .card {
    position: absolute;
    width: 525px;
    height: 299px;
    background: var(--card);
    border-radius: 20px;
    overflow: hidden;
    box-shadow: 0 4px 10px rgba(0,0,0,0.25);
  }
  .card--front { left: 337px; top: 73px; }
  .card--back-one { left: 53px; top: 446px; }
  .card--back-two { left: 621px; top: 441px; }

  .centered { position: absolute; left: 0; right: 0; text-align: center; }

  .tagline { font-size: 12.5px; color: var(--ink); }

  .wordmark { color: var(--brand-blue); line-height: 1; }
  .wordmark__name { display: block; letter-spacing: 0.5px; }
  .wordmark__sub { display: block; }
  .wordmark__dot {
    display: inline-block;
    background: var(--brand-blue);
    border-radius: 50%;
    vertical-align: middle;
  }

  /* Front */
  .card--front .tagline { top: 21px; }
  .card--front .wordmark { top: 60px; }
  .card--front .wordmark__name { font-size: 52px; }
  .card--front .wordmark__sub { font-size: 15px; margin-top: 2px; }
  .card--front .wordmark__dot { width: 12px; height: 12px; margin-right: 8px; margin-bottom: 6px; }
  .pitch { top: 153px; font-size: 12px; color: var(--brand-blue); }
  .owner { top: 181px; font-size: 17px; color: var(--brand-blue-deep); font-family: "Open Sans", Arial, sans-serif; font-weight: 600; }
  .owner__role { font-weight: 400; font-size: 14px; }
  .phone { top: 202px; font-size: 20px; color: var(--ink); font-family: "Open Sans", Arial, sans-serif; letter-spacing: 0.5px; }
  .bands { position: absolute; left: 0; top: 230px; }
  .band-text {
    position: absolute;
    font-family: "Open Sans", Arial, sans-serif;
    color: #ffffff;
  }
  .band-text--email { left: 45px; top: 239px; font-size: 17px; }
  .band-text--web { left: 300px; top: 256px; font-size: 17px; }

  /* Back one */
  .figure-art {
    position: absolute;
    left: 40px; top: 20px;
    width: 150px; height: 262px;
    background: linear-gradient(180deg, #1a4c85 0%, #2a62a0 100%);
    border-radius: 60px 60px 12px 12px;
  }
  .card--back-one .wordmark { position: absolute; left: 255px; top: 24px; }
  .card--back-one .wordmark__name { font-size: 28px; }
  .card--back-one .wordmark__sub { font-size: 10px; margin-top: 1px; }
  .card--back-one .wordmark__dot { width: 7px; height: 7px; margin-right: 5px; margin-bottom: 3px; }
  .points {
    position: absolute; left: 258px; top: 115px;
    list-style: none;
    font-family: "Open Sans", Arial, sans-serif;
    font-size: 16px; color: #111;
  }
  .points li { position: relative; padding-left: 26px; height: 33px; }
  .points li:last-child { margin-top: 3px; }
  .points li::before {
    content: ""; position: absolute; left: 2px; top: 8px;
    width: 6px; height: 6px; background: #111;
  }
  .card--back-one .site { position: absolute; left: 256px; top: 253px; font-size: 19px; color: var(--ink); font-family: "Open Sans", Arial, sans-serif; }

  /* Back two */
  .card--back-two .tagline { top: 20px; }
  .card--back-two .wordmark { top: 84px; }
  .card--back-two .wordmark__name { font-size: 74px; }
  .card--back-two .wordmark__sub { font-size: 22px; margin-top: 4px; }
  .card--back-two .wordmark__dot { width: 16px; height: 16px; margin-right: 12px; margin-bottom: 10px; }
  .card--back-two .site { top: 253px; font-size: 19px; letter-spacing: 4px; color: var(--ink-soft); font-family: "Open Sans", Arial, sans-serif; }
</style>
</head>
<body>

<span class="view-label" style="left:600px; top:33px;">Front</span>
<span class="view-label" style="left:322px; top:403px;">Back - 1</span>
<span class="view-label" style="left:897px; top:403px;">Back - 2</span>

<section class="card card--front">
  <p class="centered tagline">Is your body shocking for all the wrong reasons</p>
  <div class="centered wordmark">
    <span class="wordmark__name"><span class="wordmark__dot"></span>Lumen</span>
    <span class="wordmark__sub">Wellness and Fitness</span>
  </div>
  <p class="centered pitch">Give me a call and learn how to eat chocolate drink bear and have great sex</p>
  <p class="centered owner">Colin Ferrante, <span class="owner__role">Your Fitness Expert</span></p>
  <p class="centered phone">+00 555 01234</p>
  <svg class="bands" width="525" height="69" viewBox="0 0 525 69" aria-hidden="true">
    <polygon points="0,3 308,3 286,37 0,37" fill="var(--brand-blue)"/>
    <polygon points="268,20 525,20 525,59 243,59" fill="var(--band-dark)"/>
  </svg>
  <span class="band-text band-text--email">info@lumenstudio.example</span>
  <span class="band-text band-text--web">www.lumenstudio.example</span>
</section>

<section class="card card--back-one">
  <div class="figure-art" role="img" aria-label="Illustration of a man and a woman standing as blue silhouettes"></div>
  <div class="wordmark">
    <span class="wordmark__name"><span class="wordmark__dot"></span>Lumen</span>
    <span class="wordmark__sub">Wellness and Fitness</span>
  </div>
  <ul class="points">
    <li>Lorem Ipsum has been ...</li>
    <li>Lorem Ipsum has been ...</li>
    <li>Lorem Ipsum has been ...</li>
  </ul>
  <p class="site">www.lumenstudio.example</p>
</section>

<section class="card card--back-two">
  <p class="centered tagline">Is your body shocking for all the wrong reasons</p>
  <div class="centered wordmark">
    <span class="wordmark__name"><span class="wordmark__dot"></span>Lumen</span>
    <span class="wordmark__sub">Wellness and Fitness</span>
  </div>
  <p class="centered site">www.lumenstudio.example</p>
</section>

</body>
</html>
```